I would like a business card to match my truck wrap and logo. I would like the font to match my existing business card please.

Industry/Entity Type

Painter

Contact Information for Business Card

Rodrigo Fenwar 801-437-2190 Fenwarcoatings.utah@brelmox.com
SERVICES - Custom Paint & Stain, Interior & Exterior, Epoxy Coatings / Garage Floors, Cabinet Refinishing, Log Staining and Refinishing.

Requirements
Nice to have
• I would like to have the white and grey line like the bottom of my vehicle wrap, Light Grey to match my truck also.

```html
<!DOCTYPE html>
<html lang="en">
<head>
<meta charset="UTF-8">
<title>Fenwar Painting – Business Card</title>
<link href="https://fonts.googleapis.com/css2?family=Michroma&family=Russo+One&family=Arimo:wght@400;700&display=swap" rel="stylesheet">
<style>
  :root {
    --backdrop: #e4e5e7;
    --blue-bright: #04aef0;
    --blue-mid: #0a8fd6;
    --blue-deep: #13589a;
    --brand-cyan: #0ba7e8;
    --name-navy: #1d4f8c;
    --ink: #2b2f36;
    --white: #ffffff;
  }
  * { box-sizing: border-box; margin: 0; padding: 0; }
  html, body {
    width: 1200px; height: 900px; overflow: hidden;
    background: var(--backdrop);
  }
  .canvas { position: relative; width: 1200px; height: 900px; }

  .card {
    position: absolute; top: 217px; width: 309px; height: 500px;
    box-shadow: 2px 3px 5px rgba(0,0,0,0.18);
    overflow: hidden;
  }

  /* Front: services side */
  .card--front {
    left: 279px;
    border-radius: 0 38px 0 38px;
    background:
      radial-gradient(ellipse 70% 55% at 40% 45%, rgba(4,174,240,0.9), rgba(4,174,240,0) 70%),
      linear-gradient(160deg, var(--blue-bright) 0%, var(--blue-mid) 35%, var(--blue-deep) 75%, var(--blue-mid) 100%);
    color: var(--white);
    font-family: "Arimo", sans-serif;
  }
  .wordmark { position: absolute; left: 0; right: 0; text-align: center; font-family: "Michroma", sans-serif; }
  .wordmark__name { font-size: 34px; line-height: 1; letter-spacing: 1px; }
  .wordmark__trade { font-size: 15px; line-height: 1; letter-spacing: 14px; margin-right: -14px; margin-top: 14px; }
  .card--front .wordmark { top: 136px; color: var(--white); }

  .services { position: absolute; left: 37px; top: 312px; }
  .services__title { font-weight: 700; font-size: 17px; letter-spacing: 0.3px; margin-bottom: 14px; }
  .services__list { list-style: none; }
  .services__item {
    position: relative; padding-left: 20px;
    font-size: 14.6px; line-height: 24.5px;
  }
  .services__item::before {
    content: ""; position: absolute; left: 2px; top: 7px;
    width: 9px; height: 9px; background: var(--white); transform: rotate(45deg);
  }

  /* Back: contact side */
  .card--back {
    left: 617px;
    border-radius: 38px 0 38px 0;
    background: var(--white);
    font-family: "Arimo", sans-serif;
    color: var(--ink);
  }
  .card--back .wordmark { top: 178px; color: var(--brand-cyan); }

  .contact { position: absolute; left: 28px; top: 357px; }
  .contact__name {
    font-family: "Russo One", sans-serif; font-size: 18.5px;
    color: var(--name-navy); letter-spacing: 0.6px; margin-bottom: 30px;
  }
  .contact__line { display: flex; align-items: center; gap: 5px; font-size: 14.5px; line-height: 18px; }
  .contact__icon { width: 14px; height: 14px; flex: none; }
</style>
</head>
<body>
<main class="canvas">

  <section class="card card--front" aria-label="Card front: services">
    <div class="wordmark">
      <div class="wordmark__name">FENWAR</div>
      <div class="wordmark__trade">PAINTING</div>
    </div>
    <div class="services">
      <h2 class="services__title">SERVICES</h2>
      <ul class="services__list">
        <li class="services__item">Custom Paint &amp; Stain</li>
        <li class="services__item">Interior &amp; Exterior</li>
        <li class="services__item">Epoxy Coatings/ Garage Floors</li>
        <li class="services__item">Cabinet Refinishing</li>
        <li class="services__item">Log Staining and Refinishing.</li>
      </ul>
    </div>
  </section>

  <section class="card card--back" aria-label="Card back: contact">
    <div class="wordmark">
      <div class="wordmark__name">FENWAR</div>
      <div class="wordmark__trade">PAINTING</div>
    </div>
    <div class="contact">
      <p class="contact__name">RODRIGO FENWAR</p>
      <p class="contact__line">
        <svg class="contact__icon" viewBox="0 0 24 24" aria-hidden="true">
          <path fill="#1d6fb8" d="M6.6 10.8a15.1 15.1 0 0 0 6.6 6.6l2.2-2.2c.3-.3.7-.4 1-.2 1.1.4 2.3.6 3.6.6.6 0 1 .4 1 1V20c0 .6-.4 1-1 1A17 17 0 0 1 3 4c0-.6.4-1 1-1h3.5c.6 0 1 .4 1 1 0 1.3.2 2.5.6 3.6.1.3 0 .7-.2 1z"/>
        </svg>
        801-437-2190
      </p>
      <p class="contact__line">
        <svg class="contact__icon" viewBox="0 0 24 24" aria-hidden="true">
          <rect x="2" y="6" width="20" height="13" fill="#1d6fb8"/>
          <path d="M2 6l10 7 10-7" fill="none" stroke="#fff" stroke-width="1.6"/>
        </svg>
        Fenwarcoatings.utah@brelmox.com
      </p>
    </div>
  </section>

</main>
</body>
</html>
```